Brightway Haus Inc. Business Card Design

Brightway Haus Inc. is in search of a great clean design for our business cards!

Looking to incorporate our full logo and watermark on side one (however, I am open to having the text and watermark separated within the design.)

On side two, I am looking to have contact information (Name, Position, Phone #, Email, Website (www.thebrightwayhaus.ca). Can have the logo and/or watermark as part of the design if applicable.

Please add tagline "Where Shine Counts" on either side 1 or 2. This tagline can be in a sans serif, serif or cursive font as long as it compliments overall design. Capitalization can be title or sentence case depending on how it fits within the design.

Get creative!! Looking for a clean, crisp, premium design! Looking for a glossy card finish with spot UV features when printed. Cards will also be printed with rounded corners. Standard dimensions (3.5 x 2).

Target Market(s)

B2B - primary clients are business owners or property management corporations. (residential jobs are few and far between)

Industry/Entity Type

Business

Contact Information for Business Card

- clean, crisp design
- double sided
- spot UV accents and glossy finish upon printing
- standard business card size (3.5 x 2) with rounded corners
- please see project description for requirements per side

Font styles to use
Sans Serif

Requirements
Must have
• - adequate bleeds with print ready files
• - cohesive design elements between side 1 & 2
• - spot UV elements (can be on both sides or just one, use your discretion)
• - colour pallet should match the logo file provided
• - incorporate tagline "where shine counts" (this tagline can be in a serif or sans serif font as long as it is complimentary to the overall design.
Nice to have
• - Premium elements with a clean design
Should not have
• - Please omit cartoon or whimsical like designs, think premium.
• - Colours should not stray from the pallet of the provided logo.

```html
<!DOCTYPE html>
<html lang="en">
<head>
<meta charset="utf-8">
<title>Brightway Haus Inc. Business Card</title>
<link rel="stylesheet" href="https://fonts.googleapis.com/css2?family=Roboto+Condensed:ital,wght@0,400;0,700;1,400&family=Roboto:wght@400;500&display=swap">
<style>
  :root {
    --backdrop: #2a2a2a;
    --paper: #f3f3f3;
    --teal: #12afb0;
    --navy: #1c2453;
    --ink: #4a4a4a;
    --rule: #9a9a9a;
    --white: #ffffff;
  }
  * { margin: 0; padding: 0; box-sizing: border-box; }
  html, body { width: 1200px; height: 960px; overflow: hidden; }
  body { background: var(--backdrop); position: relative; font-family: "Roboto", sans-serif; }

  .card {
    position: absolute; width: 600px; height: 342px;
    border-radius: 22px; overflow: hidden;
    box-shadow: 0 4px 10px rgba(0,0,0,.45);
  }
  .card--front { left: 314px; top: 114px; background: var(--paper); }
  .card--back { left: 311px; top: 472px; background: var(--teal); }

  .brand { position: absolute; display: flex; align-items: center; gap: 8px;
    font-family: "Roboto Condensed", sans-serif; font-weight: 700; white-space: nowrap; }
  .brand__square { display: block; background: var(--teal); }
  .card--front .brand { left: 48px; top: 140px; font-size: 27px; color: var(--navy); }
  .card--front .brand__square { width: 20px; height: 20px; }
  .card--back .brand { left: 0; right: 0; top: 142px; justify-content: center; gap: 12px;
    font-size: 46px; color: var(--white); }
  .card--back .brand__square { width: 34px; height: 34px; background: var(--white); }

  .divider { position: absolute; left: 326px; top: 66px; width: 1px; height: 192px;
    background: linear-gradient(to bottom, transparent, var(--rule) 15%, var(--rule) 85%, transparent); }

  .contact { position: absolute; left: 356px; top: 70px; color: var(--ink); }
  .contact__name { font-family: "Roboto Condensed", sans-serif; font-weight: 700; font-size: 21px;
    color: var(--teal); line-height: 24px; }
  .contact__role { font-family: "Roboto Condensed", sans-serif; font-weight: 700; font-size: 15px;
    color: var(--navy); line-height: 20px; }
  .contact__address { margin-top: 10px; font-size: 14px; line-height: 19px; }
  .contact__lines { margin-top: 9px; list-style: none; font-size: 14px; line-height: 19px; }
  .contact__lines li { display: flex; align-items: center; gap: 8px; }
  .contact__lines svg { width: 14px; height: 14px; fill: var(--teal); flex: none; }

  .band { position: absolute; left: 0; top: 300px; width: 600px; height: 27px; }
  .band__web { position: absolute; left: 0; width: 470px; top: 306px; text-align: center;
    color: var(--white); font-size: 13px; letter-spacing: 6px; line-height: 15px; }

  .tagline { position: absolute; left: 0; right: 0; top: 274px; display: flex; align-items: center;
    justify-content: center; gap: 4px; font-family: "Roboto Condensed", sans-serif; font-style: italic;
    font-size: 19px; color: var(--white); }
  .tagline__rule { width: 110px; height: 1px; }
  .tagline__rule--left { background: linear-gradient(to right, transparent, rgba(255,255,255,.85)); }
  .tagline__rule--right { background: linear-gradient(to left, transparent, rgba(255,255,255,.85)); }
</style>
</head>
<body>
  <section class="card card--front">
    <div class="brand"><span class="brand__square"></span>Brightway Haus Inc.</div>
    <div class="divider"></div>
    <div class="contact">
      <p class="contact__name">ELLIS MORROW</p>
      <p class="contact__role">CEO/FOUNDER</p>
      <p class="contact__address">214 Larkspur Court<br>Halden, Ontario 52810</p>
      <ul class="contact__lines">
        <li><svg viewBox="0 0 16 16"><path d="M3.5 1l3 3-1.6 2a9 9 0 0 0 5.1 5.1l2-1.6 3 3-2 2.5C6.5 14.5 1.5 9.5 1 3z"/></svg>555 014 2276</li>
        <li><svg viewBox="0 0 16 16"><path d="M4 0h8a1 1 0 0 1 1 1v14a1 1 0 0 1-1 1H4a1 1 0 0 1-1-1V1a1 1 0 0 1 1-1zm1 2v10h6V2zm3 11a1 1 0 1 0 0 2 1 1 0 0 0 0-2z"/></svg>555 019 8841</li>
        <li><svg viewBox="0 0 16 16"><path d="M4 1h8v4H4zM1 6h14v7h-2v-3H3v3H1zm3 5h8v4H4z"/></svg>555 013 6620</li>
        <li><svg viewBox="0 0 16 16"><path d="M1 4h14v9H1zm1 1l6 4 6-4v-.1H2z"/></svg>ellis@brightwayhaus.ca</li>
      </ul>
    </div>
    <svg class="band" viewBox="0 0 600 27" preserveAspectRatio="none" aria-hidden="true">
      <rect x="0" y="0" width="600" height="27" fill="var(--teal)"/>
      <polygon points="490,0 600,0 600,27 478,27" fill="var(--navy)"/>
    </svg>
    <p class="band__web">www.thebrightwayhaus.ca</p>
  </section>

  <section class="card card--back">
    <div class="brand"><span class="brand__square"></span>Brightway Haus Inc.</div>
    <p class="tagline"><span class="tagline__rule tagline__rule--left"></span>Where Shine Counts<span class="tagline__rule tagline__rule--right"></span></p>
  </section>
</body>
</html>
```